Construction proffessionals servicing the inner suburbs of Melbournes NorthWest specialising in aler

I would like a web site that is sharp, contemporary and simple to navigate, ie.not too many pages. i would like a home page with some info about us, who we are what our history is and my passion for building and construction based on impeccable customer focus. i would like a projects page and somewhere for clients to add testimonials. i would like a project calculator as well so prospective clients can work out a rough budget prior to contacting. i would like the colours to be in line with my logo which i have uploaded. i have many photos which can be used and can be shared via drop box when required. I would like it to be personal to capture our transparent process. i would like to add our company process as well. be brave and take risks.

Target Market(s)

People renovating and extending their homes, people needing inspections on new homes and pre-purchase inspections

Industry/Entity Type

Construction

Number of Pages Required

5+ page

Requirements
Must have
• Professional, easy to navigate, provide viewers with a happy experience, look great, contacts, project calculator, link through to my training company www.qdmn.learnhub.example also check rowenhq on instagram for pics
Nice to have
• Links to instagram, fonts to match email signature

```html
<!DOCTYPE html>
<html lang="en">
<head>
<meta charset="utf-8">
<title>Rowen Build Co</title>
<link href="https://fonts.googleapis.com/css2?family=Open+Sans:wght@400;600;700;800&display=swap" rel="stylesheet">
<style>
:root{
  --orange:#f08a1c;
  --red:#d9472b;
  --ink:#333;
  --muted:#777;
  --line:#e2e2e2;
  --dark:#2b2b2b;
  --darker:#1f1f1f;
  --panel:#3a3a3a;
  --white:#fff;
}
*{box-sizing:border-box;margin:0;padding:0}
html,body{width:855px;height:1200px;overflow:hidden;background:#fff}
body{font-family:"Open Sans",Arial,sans-serif;color:var(--ink);position:relative;font-size:9px;line-height:1.45}
.abs{position:absolute}

.site-header{left:0;top:0;width:855px;height:48px;background:var(--white);border-bottom:1px solid var(--line)}
.brand{left:68px;top:6px;height:36px;display:flex;align-items:center;gap:6px}
.brand-mark{width:16px;height:16px;background:var(--orange)}
.brand-name{font-weight:800;font-size:15px;color:var(--orange);letter-spacing:.5px}
.main-nav{right:175px;top:17px;display:flex;gap:24px;font-size:9px;color:#555}
.main-nav a{color:inherit;text-decoration:none}
.btn-enquire{right:68px;top:13px;width:92px;height:22px;background:var(--orange);color:var(--white);font-weight:700;font-size:8px;display:flex;align-items:center;justify-content:center;letter-spacing:.4px}

.hero{left:0;top:48px;width:855px;height:345px;background:linear-gradient(180deg,#d3d6d8 0%,#b3b8bb 35%,#7b7f82 62%,#5f6265 78%,#8f9294 100%)}
.hero-tagline{left:180px;top:55px}
.hero-tagline .lead{color:var(--orange);font-weight:800;font-size:16px;letter-spacing:.3px}
.hero-tagline .sub{color:var(--white);font-size:11px;font-weight:600;letter-spacing:.2px}

.welcome{left:70px;top:408px;width:185px}
.welcome h1{font-size:11px;font-weight:800;line-height:1.3;color:#222;margin-bottom:10px}
.welcome p{color:var(--muted);font-size:7.5px;margin-bottom:12px}
.contact-line{display:flex;align-items:center;gap:5px;font-size:7.5px;color:#555;margin-bottom:5px}
.contact-line svg{flex:none}

.calculator{left:268px;top:405px;width:318px;height:245px;background:var(--orange);padding:18px 16px}
.calculator h2{color:var(--white);font-size:10px;font-weight:800;letter-spacing:.4px;margin-bottom:14px}
.calc-grid{display:grid;grid-template-columns:1fr 1fr;gap:12px 10px}
.calc-field{height:22px;background:var(--white);font-size:7px;color:#888;display:flex;align-items:center;justify-content:space-between;padding:0 6px}
.calc-actions{display:flex;align-items:center;gap:12px;margin-top:18px}
.btn-submit{background:var(--red);color:var(--white);font-size:7.5px;font-weight:700;padding:6px 16px}
.calc-actions span{color:var(--white);font-size:7.5px}
.calc-result{margin-top:22px;color:var(--white);font-size:8px;display:flex;align-items:baseline;gap:8px}
.calc-result strong{font-size:15px;font-weight:800}

.top-stories{left:600px;top:405px;width:186px}
.story-photo{width:186px;height:115px;background:linear-gradient(160deg,#e8c56a,#c98f3a 55%,#7f6a55)}
.top-stories h3{font-size:10px;font-weight:800;margin:8px 0 4px}
.top-stories p{color:var(--muted);font-size:7px}
.btn-read{display:inline-block;margin-top:8px;background:var(--red);color:var(--white);font-size:7px;font-weight:700;padding:4px 10px}

.cta-row{left:70px;top:660px;width:516px;height:54px;display:flex;gap:4px}
.cta{flex:1;display:flex;align-items:center;gap:8px;padding:0 10px;color:var(--white);font-weight:800;font-size:9px;line-height:1.2}
.cta.primary{background:var(--red)}
.cta.secondary{background:var(--panel)}
.cta-icon{width:26px;height:26px;border-radius:50%;border:2px solid var(--white);flex:none;display:flex;align-items:center;justify-content:center}

.tabs{left:70px;top:734px;width:516px;height:26px;border-bottom:1px solid var(--line);display:flex}
.tab{padding:0 14px;font-size:7.5px;color:#777;display:flex;align-items:center;border:1px solid var(--line);border-bottom:none;margin-right:3px;background:#f5f5f5}
.tab.active{background:var(--white);color:var(--orange);font-weight:700}

.projects{left:70px;top:772px;width:516px;display:grid;grid-template-columns:repeat(4,1fr);gap:10px}
.project-photo{height:112px}
.p1{background:linear-gradient(180deg,#9fc1df,#b8a68b 60%,#7c8f5a)}
.p2{background:linear-gradient(180deg,#c8d7e4,#a77c62 55%,#6f6559)}
.p3{background:linear-gradient(180deg,#a6c6de,#a25a3f 55%,#8c8068)}
.p4{background:linear-gradient(180deg,#d2d9e0,#b6aa99 50%,#7a7a72)}
.project h4{font-size:7px;color:var(--orange);font-weight:700;margin-top:6px}
.project p{font-size:6.5px;color:var(--muted)}

.clients{left:600px;top:742px;width:186px;text-align:center}
.clients h3{font-size:10px;font-weight:800;text-align:left;border-bottom:1px solid var(--line);padding-bottom:5px;margin-bottom:12px}
.client-photo{width:60px;height:60px;border-radius:50%;margin:0 auto 8px;background:linear-gradient(160deg,#c9ccd0,#8d9197)}
.clients .name{color:var(--orange);font-weight:700;font-size:8px}
.clients .role{font-size:6.5px;color:#999;margin-bottom:5px}
.clients p{font-size:7px;color:var(--muted)}

.site-footer{left:0;top:1002px;width:855px;height:198px;background:var(--dark)}
.footer-cols{left:70px;top:16px;width:716px;display:grid;grid-template-columns:1.6fr 1fr 1fr .9fr;gap:24px}
.footer-cols h5{color:var(--white);font-size:8.5px;font-weight:700;margin-bottom:8px}
.footer-cols p,.footer-cols li{color:#999;font-size:7px;list-style:none;margin-bottom:3px}
.footer-cols .hl{color:var(--orange)}
.social li{display:flex;align-items:center;gap:6px;margin-bottom:6px}
.social i{width:13px;height:13px;border-radius:50%;background:#555;display:block}
.footer-bar{left:0;top:178px;width:855px;height:20px;background:var(--darker);color:#888;font-size:6.5px;display:flex;align-items:center;justify-content:center}
</style>
</head>
<body>

<header class="site-header abs">
  <div class="brand abs"><span class="brand-mark"></span><span class="brand-name">ROWEN</span></div>
  <nav class="main-nav abs"><a>Home</a><a>About us</a><a>Projects</a><a>Testimonials</a><a>Contact us</a></nav>
  <div class="btn-enquire abs">BOOK A QUOTE</div>
</header>

<section class="hero abs" role="img" aria-label="Photograph of a long concrete bridge under an overcast sky">
  <div class="hero-tagline abs">
    <div class="lead">PROVIDING QUALITY EXPERT ADVICE,</div>
    <div class="sub">COMMON SENSE AND FRIENDLY PROFESSIONAL SERVICE</div>
  </div>
</section>

<section class="welcome abs">
  <h1>WELCOME TO THE<br>ROWEN BUILD CO WEBSITE</h1>
  <p>Our team builds and renovates homes across the inner north-west suburbs. We take pride in honest advice, careful work and a clear process from the first visit to handover.</p>
  <div class="contact-line"><svg width="9" height="9" viewBox="0 0 10 10"><path d="M2 1l2 2-1 1.5c.6 1.2 1.4 2 2.5 2.5L7 6l2 2-1.5 1.5C4.5 9 1 5.5.5 2.5z" fill="#f08a1c"/></svg>Office: (03) 9000 1234</div>
  <div class="contact-line"><svg width="9" height="9" viewBox="0 0 10 10"><rect x="2.5" y=".5" width="5" height="9" rx="1" fill="#f08a1c"/></svg>Mobile: 0400 000 111</div>
  <div class="contact-line"><svg width="9" height="9" viewBox="0 0 10 10"><rect x=".5" y="2" width="9" height="6" fill="#f08a1c"/><path d="M.5 2l4.5 3.5L9.5 2" stroke="#fff" fill="none"/></svg>Email: hello@rowenhq.example</div>
</section>

<section class="calculator abs">
  <h2>PROJECT CALCULATOR</h2>
  <div class="calc-grid">
    <div class="calc-field">Select Project<span>▾</span></div>
    <div class="calc-field">Select Area<span>▾</span></div>
    <div class="calc-field">Select Type<span>▾</span></div>
    <div class="calc-field">Select Size<span>▾</span></div>
    <div class="calc-field">Select Finish<span>▾</span></div>
    <div class="calc-field">Select Level<span>▾</span></div>
  </div>
  <div class="calc-actions"><div class="btn-submit">SUBMIT NOW</div><span>Clear all</span></div>
  <div class="calc-result">Your estimation amount is <strong>$25, 000 000</strong></div>
</section>

<aside class="top-stories abs">
  <div class="story-photo" role="img" aria-label="Photograph of builders in hard hats on a site"></div>
  <h3>TOP STORIES</h3>
  <p>Read how a tired family home was opened up with a new rear extension, finished on time and on budget.</p>
  <span class="btn-read">READ MORE</span>
</aside>

<section class="cta-row abs">
  <div class="cta primary"><span class="cta-icon"><svg width="10" height="10" viewBox="0 0 10 10"><path d="M2 1l2 2-1 1.5c.6 1.2 1.4 2 2.5 2.5L7 6l2 2-1.5 1.5C4.5 9 1 5.5.5 2.5z" fill="#fff"/></svg></span>HOW CAN<br>WE HELP YOU?</div>
  <div class="cta secondary"><span class="cta-icon"><svg width="10" height="10" viewBox="0 0 10 10"><path d="M5 1v5M5 8v1" stroke="#fff" stroke-width="1.6"/></svg></span>DO YOU HAVE A<br>BUILDING ISSUE?</div>
  <div class="cta secondary"><span class="cta-icon"><svg width="10" height="10" viewBox="0 0 10 10"><path d="M2 5.5l2 2L8 2.5" stroke="#fff" stroke-width="1.6" fill="none"/></svg></span>DO YOU NEED<br>BUILDING ADVICE</div>
</section>

<nav class="tabs abs">
  <div class="tab active">Recent Projects</div>
  <div class="tab">Upcoming Projects</div>
  <div class="tab">Government Projects</div>
</nav>

<section class="projects abs">
  <article class="project"><div class="project-photo p1" role="img" aria-label="Photograph of a renovated brick house"></div><h4>Rear extension, Brunswick</h4><p>Open plan living and deck</p><p>Completed: 2023</p></article>
  <article class="project"><div class="project-photo p2" role="img" aria-label="Photograph of a weatherboard home"></div><h4>Weatherboard restump</h4><p>Full restump and reclad</p><p>Completed: 2023</p></article>
  <article class="project"><div class="project-photo p3" role="img" aria-label="Photograph of a red brick cottage"></div><h4>Kitchen and bath refit</h4><p>New wet areas and joinery</p><p>Completed: 2022</p></article>
  <article class="project"><div class="project-photo p4" role="img" aria-label="Photograph of a house under construction"></div><h4>Second storey addition</h4><p>Two bedrooms and ensuite</p><p>Completed: 2022</p></article>
</section>

<aside class="clients abs">
  <h3>CLIENTS SAYS</h3>
  <div class="client-photo" role="img" aria-label="Portrait photograph of a client"></div>
  <div class="name">Marla Quint</div>
  <div class="role">Homeowner, Coburg</div>
  <p>The team explained every step, kept the site tidy and finished our extension exactly as promised. We would build with them again.</p>
</aside>

<footer class="site-footer abs">
  <div class="footer-cols abs">
    <div><h5>LATEST NEWS</h5><p class="hl">New training courses open this spring</p><p>Our site crew has begun short courses for apprentices in the north-west.</p><p class="hl">Pre-purchase inspections now booking</p><p>Call the office to arrange a time that suits you.</p></div>
    <div><h5>WELCOME</h5><ul><li>Home</li><li>About us</li><li>Projects</li><li>Testimonials</li><li>Contact us</li></ul></div>
    <div><h5>INFORMATION</h5><ul><li>Privacy Policy</li><li>Terms and Conditions</li><li>Our Process</li></ul></div>
    <div class="social"><h5>FOLLOW US</h5><ul><li><i></i>Our page</li><li><i></i>Updates</li><li><i></i>Network</li><li><i></i>Gallery</li></ul></div>
  </div>
  <div class="footer-bar abs">© 2024 Rowen Build Co. All Rights Reserved.</div>
</footer>

</body>
</html>
```